Patent Law

Need to develop a home page for a patent lawyer.

Colors should go with logo, blues...

Company Name- Velun Tresk, PLLC

Company Overview-

I am an Intellectual Property Lawyer and focus on patents, copyrights, trademarks, & trade secrets. I work with small businesses and start ups in the chemical and biotech industries.

Why Us-

I am small firm that can provide large-firm service at a reasonable price. I also can charge flat-fees for entreprenuers in certain practice areas.

Services-
Intellectual Property
Patents
Copyrights
Trademarks
Trade secrets
Healthcare Compliance
Elder law
Wills
Trusts

Website we like-
http://www.quorvantlegal.example/ - within industry!!
http://www.daltrowemiko.example/
http://ulbrixtane.example/
http://thegravelcounsel.example/

Target Market(s)

My customers will be small business, specifically small start-up companies in the chemical and biotech arena.

Industry/Entity Type

Trade

Requirements
Must have
• Colors should go with logo, blues...

```html
<!DOCTYPE html>
<html lang="en">
<head>
<meta charset="utf-8">
<title>Velun Tresk, PLLC — Home</title>
<link href="https://fonts.googleapis.com/css2?family=Arimo:wght@400;700&display=swap" rel="stylesheet">
<style>
:root{
  --blue:#0a7fc4;
  --blue-dark:#0574b8;
  --blue-light:#1a8fd0;
  --ink:#666;
  --page:#f2f2f2;
  --footer:#4d535b;
  --white:#fff;
}
*{margin:0;padding:0;box-sizing:border-box}
html,body{width:1200px;height:1088px;overflow:hidden}
body{font-family:"Arimo",Arial,sans-serif;background:var(--page);position:relative;color:var(--ink)}
.site-header{position:absolute;left:0;top:0;width:1200px;height:103px;background:var(--white)}
.brand{position:absolute;left:131px;top:28px;display:flex;align-items:center;gap:10px}
.brand-dot{width:34px;height:34px;border-radius:50%;background:var(--blue)}
.brand-name{font-size:16px;font-weight:700;color:#2a4a78;letter-spacing:.3px}
.contact-strip{position:absolute;right:131px;top:19px;display:flex;align-items:center;gap:8px}
.phone-number{font-size:17px;color:var(--blue);margin-right:12px}
.map-link{font-size:13px;color:#888}
.main-nav{position:absolute;right:131px;top:57px;display:flex;font-size:14px;color:#777}
.main-nav a{color:inherit;text-decoration:none;margin-left:22px}
.main-nav a.spaced{margin-left:44px}
.main-nav a.current{color:var(--blue);border-bottom:1px solid var(--blue);padding-bottom:2px}
.hero{position:absolute;left:0;top:103px;width:1200px;height:452px;
  background:linear-gradient(90deg,#3a3536 0%,#5a4a3e 25%,#b89060 50%,#c57a3a 70%,#8a4a20 100%)}
.hero-caption{position:absolute;left:0;top:366px;width:1200px;height:86px;background:rgba(20,20,20,.35);border-top:1px solid rgba(255,255,255,.35)}
.hero-caption p{position:absolute;left:132px;top:12px;width:480px;font-size:18px;line-height:38px;color:var(--white);letter-spacing:-.3px}
.read-more{position:absolute;left:926px;top:395px;width:142px;height:30px;background:var(--blue);color:var(--white);font-size:15px;text-align:center;line-height:30px}
.hero-arrow{position:absolute;top:207px}
.hero-arrow.prev{left:23px}
.hero-arrow.next{left:1139px}
.panel{position:absolute;top:589px;width:289px;height:342px;border-radius:3px;
  background:linear-gradient(180deg,var(--blue-light),var(--blue-dark));color:var(--white)}
.panel.why{left:131px}.panel.what{left:455px}.panel.contact{left:780px}
.panel-head{position:absolute;left:22px;top:18px;right:20px;border-bottom:1px solid rgba(255,255,255,.25);display:flex;align-items:center;gap:18px;padding-bottom:10px;height:58px}
.panel-icon{width:47px;height:47px;border-radius:50%;background:var(--white);display:flex;align-items:center;justify-content:center;flex:none}
.panel-title{font-size:25px;font-weight:700;letter-spacing:.2px}
.panel-body{position:absolute;left:22px;top:86px;right:18px;font-size:12px;line-height:26.3px}
.why-text+.why-text{margin-top:26px}
.service-list{list-style:none}
.service-list li{display:flex;align-items:center;gap:12px}
.contact-body{top:88px}
.greeting{font-size:13.5px;line-height:22px;margin-bottom:1px}
.contact-text{font-size:11.5px;line-height:22.5px;margin-bottom:23px}
.address-label{font-size:13px;line-height:22px;margin-bottom:4px}
.contact-line{display:flex;align-items:flex-start;gap:12px;font-size:12px;line-height:22.5px}
.contact-line svg{margin-top:7px;flex:none}
.contact-line .indent{padding-left:21px}
.site-footer{position:absolute;left:0;top:975px;width:1200px;height:113px;background:var(--footer);color:var(--white)}
.social{position:absolute;left:507px;top:-21px;display:flex;gap:1px}
.social span{width:37px;height:37px;border-radius:50%;background:var(--white);border:3px solid var(--footer);box-shadow:0 0 0 2px var(--white) inset}
.footer-links{position:absolute;top:52px;width:1200px;text-align:center;font-size:13.5px}
.footer-links span.sep{margin:0 10px}
.copyright{position:absolute;top:82px;width:1200px;text-align:center;font-size:11.5px;color:#d8d8d8}
</style>
</head>
<body>
<header class="site-header">
  <div class="brand"><span class="brand-dot"></span><span class="brand-name">VELUN TRESK, PLLC</span></div>
  <div class="contact-strip">
    <svg width="16" height="20" viewBox="0 0 16 20"><path d="M3 1l4 4-2 3c1 3 3 5 5 6l2-2 4 4-3 3C6 18 1 11 1 4z" fill="#999"/></svg>
    <span class="phone-number">411-555-0193</span>
    <svg width="14" height="20" viewBox="0 0 14 20"><path d="M7 0a7 7 0 0 1 7 7c0 5-7 13-7 13S0 12 0 7a7 7 0 0 1 7-7z" fill="#999"/><circle cx="7" cy="7" r="2.5" fill="#fff"/></svg>
    <span class="map-link">Map</span>
  </div>
  <nav class="main-nav">
    <a class="current">Home</a><a>About Us</a><a class="spaced">Firm</a><a>Media &amp; Events</a><a>Practices</a><a>FAQs</a><a>Contact Us</a>
  </nav>
</header>

<section class="hero" role="img" aria-label="Photo of attorneys seated at a conference table beside brass scales of justice">
  <svg class="hero-arrow prev" width="32" height="32" viewBox="0 0 32 32"><circle cx="16" cy="16" r="15" fill="#fff"/><path d="M19 9l-7 7 7 7" stroke="#333" stroke-width="4" fill="none"/></svg>
  <svg class="hero-arrow next" width="32" height="32" viewBox="0 0 32 32"><circle cx="16" cy="16" r="15" fill="#fff"/><path d="M13 9l7 7-7 7" stroke="#333" stroke-width="4" fill="none"/></svg>
  <div class="hero-caption"><p>We like solving your problems when they happen but love anticipating them so they don't.</p></div>
  <div class="read-more">Read More</div>
</section>

<article class="panel why">
  <div class="panel-head">
    <span class="panel-icon"><svg width="24" height="32" viewBox="0 0 24 32"><path d="M4 10a8 8 0 1 1 12 6c-3 2-4 3-4 6" stroke="#0a7fc4" stroke-width="5" fill="none"/><circle cx="12" cy="29" r="3" fill="#0a7fc4"/></svg></span>
    <h2 class="panel-title">WHY US</h2>
  </div>
  <div class="panel-body">
    <p class="why-text">Lid est laborum dolo rumes fugats untras. Eth arums ser quidem rerum facilis dolores nemis omnis fugats vitaes nemo minima rerums uns ers sadips amets.</p>
    <p class="why-text">Lid est laborum dolo rumes fugats untras. Eth arums ser quidem rerum facilis dolores nemis omnis fugats vitaes nemo minima rerums uns ers sadips amets.</p>
  </div>
</article>

<article class="panel what">
  <div class="panel-head">
    <span class="panel-icon"><svg width="28" height="28" viewBox="0 0 28 28"><circle cx="10" cy="18" r="7" fill="none" stroke="#0a7fc4" stroke-width="4" stroke-dasharray="3 2"/><circle cx="20" cy="8" r="5" fill="none" stroke="#0a7fc4" stroke-width="3" stroke-dasharray="2 2"/></svg></span>
    <h2 class="panel-title">WHAT WE DO</h2>
  </div>
  <div class="panel-body">
    <ul class="service-list">
      <li><svg width="11" height="9" viewBox="0 0 11 9"><path d="M1 5l3 3 6-7" stroke="#fff" stroke-width="2" fill="none"/></svg>Intellectual Property</li>
      <li><svg width="11" height="9" viewBox="0 0 11 9"><path d="M1 5l3 3 6-7" stroke="#fff" stroke-width="2" fill="none"/></svg>Patents</li>
      <li><svg width="11" height="9" viewBox="0 0 11 9"><path d="M1 5l3 3 6-7" stroke="#fff" stroke-width="2" fill="none"/></svg>Copyrights</li>
      <li><svg width="11" height="9" viewBox="0 0 11 9"><path d="M1 5l3 3 6-7" stroke="#fff" stroke-width="2" fill="none"/></svg>Trademarks</li>
      <li><svg width="11" height="9" viewBox="0 0 11 9"><path d="M1 5l3 3 6-7" stroke="#fff" stroke-width="2" fill="none"/></svg>Trade secrets</li>
      <li><svg width="11" height="9" viewBox="0 0 11 9"><path d="M1 5l3 3 6-7" stroke="#fff" stroke-width="2" fill="none"/></svg>Healthcare Compliance</li>
      <li><svg width="11" height="9" viewBox="0 0 11 9"><path d="M1 5l3 3 6-7" stroke="#fff" stroke-width="2" fill="none"/></svg>Elder law</li>
      <li><svg width="11" height="9" viewBox="0 0 11 9"><path d="M1 5l3 3 6-7" stroke="#fff" stroke-width="2" fill="none"/></svg>Wills</li>
      <li><svg width="11" height="9" viewBox="0 0 11 9"><path d="M1 5l3 3 6-7" stroke="#fff" stroke-width="2" fill="none"/></svg>Trusts</li>
    </ul>
  </div>
</article>

<article class="panel contact">
  <div class="panel-head">
    <span class="panel-icon"><svg width="28" height="22" viewBox="0 0 28 22"><rect x="1" y="4" width="26" height="17" fill="#0a7fc4"/><path d="M1 4l13 10 13-10" stroke="#fff" stroke-width="2" fill="none"/></svg></span>
    <h2 class="panel-title">CONTACT US</h2>
  </div>
  <div class="panel-body contact-body">
    <p class="greeting">Say Hello!</p>
    <p class="contact-text">Fusce dapibus, tellus commmcondimentum utellus fermalesuada magna. Fusce dapibus, tellus commmcondimentum......</p>
    <p class="address-label">Address:</p>
    <div class="contact-line"><svg width="9" height="12" viewBox="0 0 9 12"><path d="M4.5 0A4.5 4.5 0 0 1 9 4.5C9 8 4.5 12 4.5 12S0 8 0 4.5A4.5 4.5 0 0 1 4.5 0z" fill="#fff"/><circle cx="4.5" cy="4.5" r="1.6" fill="#0a7fc4"/></svg><span>Larkfield Street No: 22/07</span></div>
    <div class="contact-line"><span class="indent">Ferrow City, Calden</span></div>
    <div class="contact-line"><svg width="12" height="10" viewBox="0 0 12 10"><path d="M1 3c3-3 7-3 10 0v2H8V3H4v2H1z" fill="#fff"/><rect x="3" y="6" width="6" height="4" fill="#fff"/></svg><span>0247 555 01 93</span></div>
    <div class="contact-line"><svg width="12" height="9" viewBox="0 0 12 9"><rect width="12" height="9" fill="#fff"/><path d="M0 0l6 5 6-5" stroke="#0a7fc4" fill="none"/></svg><span>office@veluntresk.example</span></div>
  </div>
</article>

<footer class="site-footer">
  <div class="social"><span></span><span></span><span></span><span></span><span></span></div>
  <div class="footer-links">Privacy Policy<span class="sep">|</span>Terms of Use<span class="sep">|</span>Site Map<span class="sep">|</span>Disclaimer</div>
  <div class="copyright">20014 © Copyright&nbsp; All Rights Reserved</div>
</footer>
</body>
</html>
```